Business card for Crestline Bathrooms

Please design a business card for our bathroom renovation business. You can use my existing logo, but if you have an idea to modernize it, I would like to see it. Please see attached files first. I would like to use the blue and the orange theme. I like the concept of using the shower head in the logo. Please find following a design (or two) that I have been trying to create with my limited resources. That design was for a sign, but I was going to adopt it and use it as a business card as well. I like the concept of the water splash but I don’t think it “flows” nicely together with the logo. Another thought is that maybe creating the logo out of water splash could work and have a dramatic effect (like the water text and the butterfly picture attached with similar background instead of white). If the above doesn’t work I would like to see a modern simplified design. One of the attached files named as the unwanted business card has all the details that I want included in the business card. Please note that it is two sided.
Updates

I am very thankful for the designs that I have received, but they are very similar and only a couple of attempts to do something with the water splash as per my original brief. Modernizing the logo and having it made out of out of water splash with the orange as color accent could work and have a dramatic effect (like the water text and the butterfly picture attached with similar background instead of white). Please do not use the butterfly itself! This is just an example that images can be created out of water splash.

Contact Information for Business Card

all the details are on the unwonted business card file included

Colors
3176b5

Requirements
Nice to have
• Copied from the brief:
• ... maybe creating the logo out of water splash could work and have a dramatic effect (like the water text and the butterfly picture attached with similar background instead of white). Please do not use the butterfly itself!
Should not have
• I am getting designs with a butterfly. The butterfly picture was an example of creating something from a water splash. The butterfly itself has no association with anything other than the concept of creating a logo out of water splash. Sorry, I thought I was clear in the brief.

```html
<!DOCTYPE html>
<html lang="en">
<head>
<meta charset="utf-8">
<title>Crestline Bathrooms – Business Card</title>
<link href="https://fonts.googleapis.com/css2?family=Roboto:wght@400;500&display=swap" rel="stylesheet">
<style>
  :root {
    --backdrop: #2a2a2b;
    --card-white: #f4f4f4;
    --navy: #0f3d68;
    --navy-deep: #0c3a66;
    --water-light: #7cc6f0;
    --water-mid: #3e9fdc;
    --water-deep: #1565b0;
    --text-dark: #12375c;
    --white: #ffffff;
  }
  * { margin: 0; padding: 0; box-sizing: border-box; }
  html, body {
    width: 1200px; height: 960px; overflow: hidden;
    background: var(--backdrop);
    font-family: "Roboto", Arial, sans-serif;
  }
  .canvas { position: relative; width: 1200px; height: 960px; }

  .card {
    position: absolute; left: 320px; width: 600px;
    border-radius: 18px; overflow: hidden;
  }
  .card-front { top: 95px; height: 355px; background: var(--card-white); }
  .card-back { top: 493px; height: 342px; background: var(--navy-deep); }

  .water-band { position: absolute; left: 0; top: 0; width: 600px; height: 355px; }

  .brand {
    position: absolute; right: 52px; top: 78px;
    color: var(--navy); font-weight: 500; font-size: 34px; line-height: 1;
    text-align: right; letter-spacing: 0.5px;
  }
  .brand small { display: block; font-size: 20px; letter-spacing: 3px; margin-top: 6px; }

  .contact {
    position: absolute; left: 28px; top: 220px;
    color: var(--text-dark); font-size: 14.5px; line-height: 19px;
  }
  .contact .address { margin-bottom: 10px; }
  .contact li { list-style: none; display: flex; align-items: center; gap: 8px; }
  .contact svg { width: 13px; height: 13px; flex: none; fill: var(--text-dark); }

  .holder {
    position: absolute; right: 22px; top: 318px;
    color: var(--text-dark); font-weight: 500; font-size: 19px; letter-spacing: 0.3px;
  }

  .back-brand {
    position: absolute; left: 0; right: 0; top: 92px; text-align: center;
    color: var(--white); font-weight: 500; font-size: 36px; letter-spacing: 0.5px;
  }
  .services {
    position: absolute; left: 0; right: 0; top: 188px; text-align: center;
    color: var(--white); font-size: 14.5px; line-height: 18px;
  }
  .badges {
    position: absolute; left: 0; right: 0; top: 275px;
    display: flex; justify-content: center; align-items: center; gap: 14px;
  }
  .badge-square { width: 28px; height: 30px; background: var(--white); border-radius: 4px; }
  .badge-divider { width: 1px; height: 34px; background: var(--white); opacity: .7; }
  .badge-wide { width: 118px; height: 26px; background: var(--white); border-radius: 3px; }
</style>
</head>
<body>
<div class="canvas">

  <section class="card card-front">
    <svg class="water-band" viewBox="0 0 600 355" role="img" aria-label="Blue water wave splash with bubbles across the lower card">
      <defs>
        <linearGradient id="waterFill" x1="0" y1="0" x2="0" y2="1">
          <stop offset="0" stop-color="var(--water-deep)"/>
          <stop offset=".45" stop-color="var(--water-mid)"/>
          <stop offset="1" stop-color="var(--water-light)"/>
        </linearGradient>
      </defs>
      <path d="M0 140 C60 120 120 110 180 128 C260 150 320 200 400 205 C470 210 530 185 600 160 L600 355 L0 355 Z" fill="url(#waterFill)"/>
    </svg>

    <div class="brand">Crestline<small>Bathrooms</small></div>

    <div class="contact">
      <p class="address">PO Box 41<br>Kelvin Grove 2740</p>
      <ul>
        <li><svg viewBox="0 0 16 16"><path d="M3 1l3 3-2 2c1 2 3 4 6 6l2-2 3 3-2 2C7 15 1 9 1 3z"/></svg>0400 555 218</li>
        <li><svg viewBox="0 0 16 16"><path d="M4 0h8v16H4z M5.5 2v10h5V2z"/></svg>5550 1947</li>
        <li><svg viewBox="0 0 16 16"><path d="M1 3h14v10H1z M2 4l6 5 6-5z"/></svg>daniel@crestlinebathrooms.com.au</li>
        <li><svg viewBox="0 0 16 16"><circle cx="8" cy="8" r="7"/></svg>crestlinebathrooms.com.au</li>
      </ul>
    </div>

    <div class="holder">DANIEL MARSH</div>
  </section>

  <section class="card card-back">
    <div class="back-brand">Crestline Bathrooms</div>
    <p class="services">
      Complete Bathroom Renovations &amp; Remodelling<br>
      Highly Skilled &amp; Qualified Tradespeople<br>
      Professional Service From Concept To Completion<br>
      All Work Guaranteed
    </p>
    <div class="badges">
      <span class="badge-square"></span>
      <span class="badge-divider"></span>
      <span class="badge-wide"></span>
    </div>
  </section>

</div>
</body>
</html>
```